Quorva - corporate Business Card

We need a good look and innovative business card for a new start up company based in Los Angeles called "Quorva". We are in a payment business, including payment card, app, and ewallet. We are expert in online payment and Card not present (CNP) transaction.
We need an innovative, modern business card.

Our logo font is Aero Matics

Target Market(s)

Startup - Bank - Online Payment - Card Manufacturing

Industry/Entity Type

Startup

Contact Information for Business Card

phone: 555 014 7396 - Address: 4172 Marlowe blvd, Brenton Vale, OR 97418

Requirements
Must have
• Message: innovative, professional, expert, high tech, trust, online payment expert, security
Nice to have
• no comment
Should not have
• no Comment

```html
<!DOCTYPE html>
<html lang="en">
<head>
<meta charset="utf-8">
<title>Quorva — Business Card</title>
<link rel="stylesheet" href="https://fonts.googleapis.com/css2?family=Open+Sans:wght@300;400;600;700&display=swap">
<style>
  :root {
    --page-bg: #d9d4cd;
    --card-bg: #efedeb;
    --brand-red: #7e1118;
    --band-red: #8c161d;
    --name-red: #8a1a20;
    --title-grey: #8b8680;
    --phone-tint: rgba(255, 235, 235, 0.6);
    --ring-white: #f4f2f0;
  }
  * { box-sizing: border-box; margin: 0; padding: 0; }
  html, body {
    width: 1200px;
    height: 970px;
    overflow: hidden;
    background: var(--page-bg);
    font-family: "Open Sans", Arial, sans-serif;
  }
  .canvas {
    position: relative;
    width: 1200px;
    height: 970px;
  }
  .business-card {
    position: absolute;
    left: 75px;
    top: 179px;
    width: 1050px;
    height: 612px;
    background: var(--card-bg);
    overflow: hidden;
    box-shadow: 0 10px 30px rgba(60, 40, 30, 0.18);
  }
  .holder {
    position: absolute;
    left: 52px;
    top: 58px;
  }
  .holder-name {
    font-size: 35px;
    font-weight: 700;
    color: var(--name-red);
    line-height: 1.05;
    white-space: nowrap;
  }
  .holder-title {
    font-size: 27px;
    font-weight: 400;
    color: var(--title-grey);
    line-height: 1.05;
    white-space: nowrap;
  }
  .brand-name {
    position: absolute;
    right: 49px;
    top: 33px;
    font-size: 105px;
    font-weight: 700;
    color: var(--brand-red);
    line-height: 1.2;
    white-space: nowrap;
  }
  .band {
    position: absolute;
    left: 0;
    top: 319px;
    width: 100%;
    height: 232px;
    background: var(--band-red);
  }
  .emblem {
    position: absolute;
    left: 375px;
    top: 158px;
    width: 296px;
    height: 296px;
  }
  .phone {
    position: absolute;
    left: 0;
    top: 489px;
    width: 100%;
    display: flex;
    justify-content: center;
    align-items: center;
    gap: 10px;
    font-size: 25px;
    font-weight: 400;
    color: var(--phone-tint);
    white-space: nowrap;
  }
  .phone svg { width: 28px; height: 28px; }
  .address {
    position: absolute;
    left: 0;
    top: 560px;
    width: 100%;
    text-align: center;
    font-size: 27px;
    font-weight: 400;
    color: var(--name-red);
    white-space: nowrap;
  }
</style>
</head>
<body>
<main class="canvas">
  <section class="business-card">
    <div class="holder">
      <p class="holder-name">Nolan Reyes</p>
      <p class="holder-title">Managing Director</p>
    </div>

    <p class="brand-name">quorva</p>

    <div class="band"></div>

    <svg class="emblem" viewBox="0 0 296 296" aria-hidden="true">
      <circle cx="148" cy="148" r="148" fill="var(--ring-white)"/>
      <rect x="0" y="0" width="296" height="161" fill="var(--card-bg)"/>
      <circle cx="148" cy="148" r="134" fill="var(--brand-red)"/>
    </svg>

    <p class="phone">
      <svg viewBox="0 0 24 24" aria-hidden="true">
        <circle cx="12" cy="12" r="11" fill="currentColor"/>
        <path d="M8.2 6.5c.4-.4 1-.4 1.3 0l1.3 1.6c.3.4.3.9 0 1.2l-.8.8c.6 1.3 1.6 2.3 2.9 2.9l.8-.8c.3-.3.8-.3 1.2 0l1.6 1.3c.4.3.4.9 0 1.3l-.9.9c-.6.6-1.5.8-2.3.4-2.7-1.2-4.8-3.3-6-6-.4-.8-.2-1.7.4-2.3z" fill="var(--band-red)"/>
      </svg>
      <span>555 014 7396</span>
    </p>

    <p class="address">4172 Marlowe blvd, Brenton Vale, OR 97418</p>
  </section>
</main>
</body>
</html>
```